Stonebridge Building and Projects business cards

A business card with watermark background (construction work)

Company logo attached

Home improvement projects
House renovations
Bathroom and kitchen renovations
House extensions
New builds and granny flats

Director Omar Haddani
(Phone number)
omar@sbpbuilding.com.au
(Instagram logo) sbp_building

```html
<!DOCTYPE html>
<html lang="en">
<head>
<meta charset="utf-8">
<title>Stonebridge Building and Projects – Business Cards</title>
<link href="https://fonts.googleapis.com/css2?family=Montserrat:wght@500;600;700&family=Roboto:wght@400;500;700&display=swap" rel="stylesheet">
<style>
  :root{
    --bg:#2a2a2b;
    --card:#f7f7f7;
    --blue:#1877c4;
    --ink:#2f2f33;
    --muted:#55575c;
    --rule:#1877c4;
    --faint:#e9e9ea;
  }
  *{box-sizing:border-box;margin:0;padding:0}
  html,body{width:1200px;height:1050px;overflow:hidden;background:var(--bg)}
  body{position:relative;font-family:"Roboto",Arial,sans-serif;color:var(--ink)}

  .card{position:absolute;left:280px;width:640px;height:366px;background:var(--card);
        border-radius:22px;overflow:hidden;box-shadow:0 10px 24px rgba(0,0,0,.45)}
  .card--services{top:120px}
  .card--contact{top:560px}

  .watermark{position:absolute;border-radius:8px;
             background:linear-gradient(135deg,var(--faint),rgba(233,233,234,0))}
  .card--services .watermark{left:300px;top:20px;width:300px;height:300px}
  .card--contact .watermark{left:420px;top:40px;width:200px;height:160px}

  .brand{position:absolute}
  .brand__row{display:flex;align-items:center;gap:10px}
  .brand__mark{width:18px;height:18px;background:var(--blue)}
  .brand__name{font-family:"Montserrat",Arial,sans-serif;font-weight:700;color:var(--blue);
               font-size:24px;line-height:1.1;max-width:230px}
  .brand__tagline{margin-top:8px;font-family:"Roboto",Arial,sans-serif;font-weight:500;
                  color:var(--blue);font-size:17px;display:inline-block;
                  border-top:2px solid var(--rule);border-bottom:2px solid var(--rule);padding:2px 0}

  .card--services .brand{left:44px;top:120px}

  .services{position:absolute;left:345px;top:60px;list-style:none;font-size:16px;line-height:1.55;color:var(--muted)}
  .services li{position:relative;padding-left:22px;max-width:250px}
  .services li::before{content:"";position:absolute;left:0;top:8px;width:8px;height:8px;
                       background:radial-gradient(circle,var(--blue) 1.4px,transparent 1.6px) 0 0/4px 4px}

  .social-tab{position:absolute;right:0;bottom:0;width:290px;height:60px;background:var(--blue);
              border-top-left-radius:18px;display:flex;align-items:center;padding-left:40px;
              color:#fff;font-size:15px;gap:10px}
  .card--services .band{position:absolute;right:0;bottom:60px;width:310px;height:3px;background:var(--blue)}

  .icon{width:16px;height:16px;flex:none}

  .side-stripe{position:absolute;left:0;top:0;width:52px;height:100%;background:var(--blue)}
  .side-rule{position:absolute;left:62px;top:0;width:3px;height:100%;background:var(--ink)}

  .card--contact .brand{left:110px;top:48px}
  .card--contact .top-rule{position:absolute;left:330px;top:150px;width:280px;height:1px;background:var(--ink)}

  .person{position:absolute;left:110px;top:215px}
  .person__name{font-weight:700;color:var(--blue);font-size:21px}
  .person__title{font-size:15px;color:var(--muted);margin-top:2px}
  .person__rule{position:absolute;left:290px;top:225px;width:320px;height:2px;background:var(--blue)}

  .contacts{list-style:none;font-size:15px;color:var(--muted)}
  .contacts li{display:flex;align-items:center;gap:10px;margin-bottom:8px}
  .contacts--left{position:absolute;left:110px;top:280px}
  .contacts--right{position:absolute;left:360px;top:250px}
</style>
</head>
<body>

<section class="card card--services" aria-label="Services side">
  <div class="watermark" role="img" aria-label="Faint construction work background"></div>
  <div class="brand">
    <div class="brand__row"><span class="brand__mark"></span><span class="brand__name">Stonebridge Building and Projects</span></div>
    <span class="brand__tagline">Built right, built once!</span>
  </div>
  <ul class="services">
    <li>Home improvement projects</li>
    <li>House renovations</li>
    <li>Bathroom and kitchen renovations</li>
    <li>House extensions</li>
    <li>New builds and granny flats</li>
  </ul>
  <div class="band"></div>
  <div class="social-tab">
    <svg class="icon" viewBox="0 0 16 16"><circle cx="8" cy="8" r="6" fill="none" stroke="#fff" stroke-width="1.6"/></svg>
    <span>sbp_building</span>
  </div>
</section>

<section class="card card--contact" aria-label="Contact side">
  <div class="side-stripe"></div>
  <div class="side-rule"></div>
  <div class="watermark" role="img" aria-label="Faint construction work background"></div>
  <div class="brand">
    <div class="brand__row"><span class="brand__mark"></span><span class="brand__name">Stonebridge Building and Projects</span></div>
    <span class="brand__tagline">Built right, built once!</span>
  </div>
  <div class="top-rule"></div>

  <div class="person">
    <div class="person__name">Omar Haddani</div>
    <div class="person__title">Managing Director</div>
  </div>
  <div class="person__rule"></div>

  <ul class="contacts contacts--left">
    <li>
      <svg class="icon" viewBox="0 0 16 16"><path d="M4 2l2.5 3-1.5 1.5a8 8 0 004.5 4.5L11 9.5l3 2.5-1.5 2C7 14 2 9 2 3.5z" fill="none" stroke="#1877c4" stroke-width="1.4"/></svg>
      <span>0400 318 275</span>
    </li>
    <li>
      <svg class="icon" viewBox="0 0 16 16"><circle cx="8" cy="8" r="6" fill="none" stroke="#1877c4" stroke-width="1.6"/></svg>
      <span>sbp_building</span>
    </li>
  </ul>

  <ul class="contacts contacts--right">
    <li>
      <svg class="icon" viewBox="0 0 16 16"><rect x="1.5" y="3.5" width="13" height="9" fill="none" stroke="#1877c4" stroke-width="1.4"/><path d="M1.5 3.5L8 9l6.5-5.5" fill="none" stroke="#1877c4" stroke-width="1.4"/></svg>
      <span>omar@sbpbuilding.com.au</span>
    </li>
    <li>
      <svg class="icon" viewBox="0 0 16 16"><circle cx="8" cy="8" r="6.3" fill="none" stroke="#1877c4" stroke-width="1.4"/><path d="M1.7 8h12.6M8 1.7c-3 3.5-3 9 0 12.6M8 1.7c3 3.5 3 9 0 12.6" fill="none" stroke="#1877c4" stroke-width="1.2"/></svg>
      <span>www.sbpbuilding.com.au</span>
    </li>
  </ul>
</section>

</body>
</html>
```